Pyschiatry Experts need Marketing Campaign

Ad(s) developed for print advertising sharing our purpose and services, highlighting our medical care providers. Must be welcoming and inviting while displaying a high level of professionalism expected from a physician's office.

Target Market(s)

Local community

Industry/Entity Type

Psychiatry (Healthcare)

Requirements
Must have
• Staff pictures, 'Medication Management Experts', 'Prompt Appointments', 'ADD/ADHD, Bipolar Disorder, Depression, Anxiety, Schizophrenia, Grief Reaction and others' 'Virtual and In-Person Visits'
Nice to have
• Address: 412 E Marlowe Coeur d'Alene Phone (208)555-7193 website: BrightLoftCare.com Hours: Mon - Thur 7am - 6pm

```html
<!DOCTYPE html>
<html lang="en">
<head>
<meta charset="utf-8">
<title>Bright Loft Care – Mental Health Evaluations</title>
<link rel="stylesheet" href="https://fonts.googleapis.com/css2?family=Montserrat:wght@400;800&family=Oswald:wght@700&family=Poppins:wght@400;500;600;700;800&display=swap">
<style>
  :root {
    --teal: #12927f;
    --forest: #0b3a22;
    --lime: #8fd14f;
    --cream: #f3eedc;
    --ink: #333333;
    --grey-bg: #777777;
    --soft-grey: #e6e6e6;
    --white: #ffffff;
  }
  * { margin: 0; padding: 0; box-sizing: border-box; }
  html, body { width: 1200px; height: 938px; overflow: hidden; background: var(--grey-bg); }
  .canvas { position: relative; width: 1200px; height: 938px; }
  .flyer {
    position: absolute; left: 78px; top: 106px; width: 1045px; height: 726px;
    background: var(--white); overflow: hidden;
    box-shadow: 0 10px 30px rgba(0,0,0,.35);
    font-family: "Poppins", sans-serif;
  }
  .shapes { position: absolute; inset: 0; }
  .headline { position: absolute; left: 78px; top: 38px; color: var(--white); }
  .headline__kicker { font-family: "Montserrat", sans-serif; font-weight: 400; font-size: 27px; letter-spacing: 9px; line-height: 1; margin-left: 4px; }
  .headline__main { font-family: "Montserrat", sans-serif; font-weight: 800; font-size: 63px; line-height: 58px; margin-top: 4px; letter-spacing: .5px; }

  .spectrum-title {
    position: absolute; left: 24px; top: 326px; width: 180px; text-align: center;
    font-family: "Oswald", sans-serif; font-weight: 700; font-size: 24px; line-height: 25px;
    color: var(--forest); transform: scaleX(.92);
  }
  .condition { position: absolute; font-weight: 600; font-size: 18px; line-height: 22px; color: var(--ink); }
  .condition-icon { position: absolute; width: 46px; height: 46px; }

  .perk {
    position: absolute; height: 56px; border-radius: 18px;
    background: var(--forest); border: 2px solid var(--lime);
    color: var(--white); font-weight: 700; font-size: 15px; line-height: 19px;
    padding: 8px 0 0 38px; letter-spacing: .2px;
  }
  .perk-check { position: absolute; width: 36px; height: 36px; }

  .brand { position: absolute; left: 325px; top: 596px; width: 230px; text-align: center; }
  .brand__dot { display: block; width: 34px; height: 34px; border-radius: 50%; background: var(--teal); margin: 0 auto 8px; }
  .brand__name { font-weight: 600; font-size: 24px; color: var(--teal); letter-spacing: 1.5px; line-height: 1; }

  .team-title {
    position: absolute; left: 524px; top: 304px;
    font-weight: 800; font-size: 26px; line-height: 24px; color: var(--forest); letter-spacing: .3px;
  }
  .card {
    position: absolute; height: 68px; border-radius: 10px; background: var(--cream);
  }
  .card__photo {
    position: absolute; left: 0; top: -2px; width: 72px; height: 70px; border-radius: 8px;
    background: linear-gradient(160deg, #c9d2da, #5d6b78);
    border: 2px solid var(--white);
  }
  .card__name { position: absolute; left: 86px; top: 14px; font-weight: 700; font-size: 15.5px; color: var(--forest); line-height: 1; }
  .card__cred { position: absolute; left: 86px; top: 38px; font-weight: 500; font-size: 12.5px; color: var(--forest); line-height: 1; letter-spacing: .5px; }

  .contact { position: absolute; color: var(--white); }
  .hours { left: 558px; top: 555px; font-weight: 700; font-size: 21px; white-space: nowrap; display: flex; align-items: center; gap: 10px; }
  .hours svg { width: 14px; height: 14px; }
  .info-line { position: absolute; left: 605px; display: flex; align-items: center; gap: 12px; color: var(--white); white-space: nowrap; }
  .info-line svg { width: 18px; height: 18px; flex: none; }
  .info-phone { top: 601px; font-weight: 700; font-size: 22px; }
  .info-addr { top: 632px; font-weight: 400; font-size: 18px; }
  .info-web { top: 656px; font-weight: 400; font-size: 18px; }
</style>
</head>
<body>
<div class="canvas">
  <div class="flyer">
    <svg class="shapes" width="1045" height="726" viewBox="0 0 1045 726">
      <!-- header band -->
      <path d="M0,0 H780 L700,60 C640,150 620,195 560,205 C430,225 300,225 0,178 Z" fill="var(--teal)"/>
      <!-- spectrum ring -->
      <circle cx="110" cy="378" r="112" fill="var(--soft-grey)" role="img" aria-label="Faint illustration of a head profile with a brain"/>
      <path d="M4,268 A156,156 0 0 1 164,232" fill="none" stroke="var(--lime)" stroke-width="5"/>
      <path d="M4,488 A156,156 0 0 0 164,524" fill="none" stroke="var(--lime)" stroke-width="5"/>
      <!-- contact panel -->
      <path d="M494,550 C640,515 820,472 1045,452 V726 H578 C568,650 545,590 494,550 Z" fill="var(--forest)"/>
      <!-- photo ring -->
      <circle cx="873" cy="138" r="188" fill="var(--white)"/>
      <circle cx="873" cy="138" r="178" fill="#d9d4cc" role="img" aria-label="Photo of a smiling woman in a yellow top sitting on a sofa using her phone"/>
      <path d="M705,200 A178,178 0 0 0 1040,220" fill="none" stroke="var(--lime)" stroke-width="4"/>
    </svg>

    <div class="headline">
      <div class="headline__kicker">COMPREHENSIVE</div>
      <div class="headline__main">MENTAL HEALTH<br>EVALUATIONS</div>
    </div>

    <div class="spectrum-title">EXPERTS<br>IN THE ENTIRE<br>MENTAL HEALTH<br>SPECTRUM:</div>

    <svg class="condition-icon" style="left:175px;top:233px" viewBox="0 0 46 46"><circle cx="23" cy="23" r="21" fill="var(--forest)" stroke="var(--lime)" stroke-width="3"/><circle cx="23" cy="23" r="9" fill="none" stroke="#fff" stroke-width="2"/></svg>
    <div class="condition" style="left:241px;top:244px">ADD/ADHD</div>

    <svg class="condition-icon" style="left:214px;top:277px" viewBox="0 0 46 46"><circle cx="23" cy="23" r="21" fill="var(--forest)" stroke="var(--lime)" stroke-width="3"/><circle cx="23" cy="23" r="9" fill="none" stroke="#fff" stroke-width="2"/></svg>
    <div class="condition" style="left:269px;top:292px">Bipolar Disorder</div>

    <svg class="condition-icon" style="left:225px;top:329px" viewBox="0 0 46 46"><circle cx="23" cy="23" r="21" fill="var(--forest)" stroke="var(--lime)" stroke-width="3"/><rect x="15" y="15" width="16" height="16" rx="2" fill="none" stroke="#fff" stroke-width="2"/></svg>
    <div class="condition" style="left:283px;top:347px">Prompt Appointments</div>

    <svg class="condition-icon" style="left:225px;top:379px" viewBox="0 0 46 46"><circle cx="23" cy="23" r="21" fill="var(--forest)" stroke="var(--lime)" stroke-width="3"/><circle cx="23" cy="23" r="9" fill="none" stroke="#fff" stroke-width="2"/></svg>
    <div class="condition" style="left:281px;top:397px">Depression, Anxiety</div>

    <svg class="condition-icon" style="left:210px;top:433px" viewBox="0 0 46 46"><circle cx="23" cy="23" r="21" fill="var(--forest)" stroke="var(--lime)" stroke-width="3"/><circle cx="23" cy="23" r="9" fill="none" stroke="#fff" stroke-width="2"/></svg>
    <div class="condition" style="left:272px;top:448px">Schizophrenia</div>

    <svg class="condition-icon" style="left:175px;top:483px" viewBox="0 0 46 46"><circle cx="23" cy="23" r="21" fill="var(--forest)" stroke="var(--lime)" stroke-width="3"/><circle cx="23" cy="23" r="9" fill="none" stroke="#fff" stroke-width="2"/></svg>
    <div class="condition" style="left:242px;top:495px">Grief Reaction<br>and others</div>

    <div class="perk" style="left:74px;top:565px;width:192px">PROMPT<br>APPOINTMENTS</div>
    <div class="perk" style="left:70px;top:626px;width:206px">VIRTUAL AND<br>IN-PERSON VISITS</div>
    <svg class="perk-check" style="left:62px;top:572px" viewBox="0 0 36 36"><circle cx="18" cy="18" r="16" fill="var(--forest)" stroke="var(--lime)" stroke-width="3"/><circle cx="18" cy="18" r="9" fill="var(--lime)"/><path d="M13.5,18 l3,3 l6,-6" fill="none" stroke="var(--forest)" stroke-width="2.2"/></svg>
    <svg class="perk-check" style="left:62px;top:636px" viewBox="0 0 36 36"><circle cx="18" cy="18" r="16" fill="var(--forest)" stroke="var(--lime)" stroke-width="3"/><circle cx="18" cy="18" r="9" fill="var(--lime)"/><path d="M13.5,18 l3,3 l6,-6" fill="none" stroke="var(--forest)" stroke-width="2.2"/></svg>

    <div class="brand">
      <span class="brand__dot"></span>
      <div class="brand__name">BRIGHT LOFT CARE</div>
    </div>

    <div class="team-title">MEDICATION<br>MANAGEMENT EXPERTS</div>

    <div class="card" style="left:530px;top:374px;width:212px">
      <div class="card__photo" role="img" aria-label="Staff portrait of Mark Dalton"></div>
      <div class="card__name">Mark Dalton</div><div class="card__cred">PMHNP - BC</div>
    </div>
    <div class="card" style="left:755px;top:374px;width:222px">
      <div class="card__photo" role="img" aria-label="Staff portrait of Laura Whitcomb"></div>
      <div class="card__name">Laura Whitcomb</div><div class="card__cred">PMHNP - BC</div>
    </div>
    <div class="card" style="left:530px;top:456px;width:212px">
      <div class="card__photo" role="img" aria-label="Staff portrait of Greg Harlan"></div>
      <div class="card__name">Greg Harlan</div><div class="card__cred">PMHNP - BC</div>
    </div>
    <div class="card" style="left:755px;top:456px;width:222px">
      <div class="card__photo" role="img" aria-label="Staff portrait of Ellen Prescott"></div>
      <div class="card__name">Ellen Prescott</div><div class="card__cred">PMHNP-BC, DNP</div>
    </div>

    <div class="contact hours">
      <span>HOURS:</span>
      <svg viewBox="0 0 14 14"><rect x="1" y="2" width="12" height="11" fill="none" stroke="var(--lime)" stroke-width="2"/><line x1="1" y1="6" x2="13" y2="6" stroke="var(--lime)" stroke-width="2"/></svg>
      <span>Mon - Thur</span>
      <svg viewBox="0 0 14 14" style="margin-left:10px"><circle cx="7" cy="7" r="6" fill="none" stroke="var(--lime)" stroke-width="2"/><path d="M7,4 V7 H9.5" fill="none" stroke="var(--lime)" stroke-width="1.6"/></svg>
      <span>7AM - 6PM</span>
    </div>
    <div class="info-line info-phone">
      <svg viewBox="0 0 18 18"><circle cx="9" cy="9" r="9" fill="var(--lime)"/><path d="M6,4.5 l2,2 l-1,1.3 c.8,1.5 1.8,2.5 3.2,3.2 l1.3,-1 l2,2 l-1.3,1.5 c-3.5,-.3 -7,-3.8 -7.4,-7.4 Z" fill="var(--forest)"/></svg>
      <span>(208)555-7193</span>
    </div>
    <div class="info-line info-addr">
      <svg viewBox="0 0 18 18"><path d="M9,1 C5.5,1 3,3.5 3,7 C3,11 9,17 9,17 C9,17 15,11 15,7 C15,3.5 12.5,1 9,1 Z" fill="var(--lime)"/><circle cx="9" cy="7" r="2.3" fill="var(--forest)"/></svg>
      <span>412 E Marlowe Coeur d'Alene</span>
    </div>
    <div class="info-line info-web">
      <svg viewBox="0 0 18 18"><circle cx="9" cy="9" r="8" fill="var(--lime)"/><ellipse cx="9" cy="9" rx="3.3" ry="7" fill="none" stroke="var(--forest)" stroke-width="1.2"/><line x1="1.5" y1="9" x2="16.5" y2="9" stroke="var(--forest)" stroke-width="1.2"/></svg>
      <span>BrightLoftCare.com</span>
    </div>
  </div>
</div>
</body>
</html>
```